Corporate Business Card

Very professional, Modern, Not to busy, include phone address email, website
(253) 617-4930, 18761 52nd Avenue S, Kent, WA 98047, martin@plumlinegroup.com, varkoworks.com

Target Market(s)

Manufacturing

Industry/Entity Type

Aero, machining, manufacturing, Off road racing

Contact Information for Business Card

Phone, address email, website

```html
<!DOCTYPE html>
<html lang="en">
<head>
<meta charset="utf-8">
<title>Varko Works – Business Card</title>
<link href="https://fonts.googleapis.com/css2?family=Exo+2:wght@700&family=Abel&display=swap" rel="stylesheet">
<style>
  :root {
    --navy: #1b3a78;
    --red: #d6262d;
    --ink: #444a52;
    --card: #ffffff;
    --card-shade: #ececec;
    --backdrop: #d9dadc;
  }
  * { box-sizing: border-box; margin: 0; padding: 0; }
  html, body { width: 1200px; height: 900px; overflow: hidden; }
  body {
    background: var(--backdrop);
    display: flex;
    flex-direction: column;
    align-items: center;
    justify-content: center;
    gap: 44px;
  }
  .card {
    width: 640px;
    height: 366px;
    border-radius: 34px;
    background: linear-gradient(120deg, var(--card-shade), var(--card) 60%);
    box-shadow: 0 10px 28px rgba(0,0,0,0.18);
    position: relative;
  }
  .brand {
    display: flex;
    align-items: center;
    gap: 12px;
  }
  .brand-mark {
    width: 16px; height: 16px;
    background: var(--red);
  }
  .brand-name {
    font-family: "Exo 2", sans-serif;
    font-weight: 700;
    font-size: 44px;
    color: var(--navy);
    letter-spacing: 0.5px;
  }
  .card-front {
    display: flex;
    align-items: center;
    justify-content: center;
  }
  .card-back .brand {
    position: absolute;
    left: 48px;
    top: 160px;
  }
  .card-back .brand-name { font-size: 36px; }
  .divider {
    position: absolute;
    left: 338px;
    top: 78px;
    width: 2px;
    height: 210px;
    background: var(--red);
  }
  .contact-list {
    position: absolute;
    left: 370px;
    top: 100px;
    list-style: none;
    font-family: "Abel", sans-serif;
    font-size: 19px;
    color: var(--ink);
  }
  .contact-list li {
    display: flex;
    align-items: flex-start;
    gap: 10px;
    margin-bottom: 14px;
    line-height: 1.25;
  }
  .contact-list svg {
    width: 16px; height: 16px;
    flex: none;
    margin-top: 3px;
    fill: var(--navy);
  }
</style>
</head>
<body>
  <section class="card card-front">
    <div class="brand">
      <span class="brand-mark"></span>
      <span class="brand-name">Varko Works</span>
    </div>
  </section>

  <section class="card card-back">
    <div class="brand">
      <span class="brand-mark"></span>
      <span class="brand-name">Varko Works</span>
    </div>
    <div class="divider"></div>
    <ul class="contact-list">
      <li>
        <svg viewBox="0 0 16 16"><path d="M3 2h3l1.5 3.5-2 1.2a8 8 0 0 0 3.8 3.8l1.2-2L14 10v3a1 1 0 0 1-1 1A11 11 0 0 1 2 3a1 1 0 0 1 1-1z"/></svg>
        (253) 617-4930
      </li>
      <li>
        <svg viewBox="0 0 16 16"><path d="M8 1a7 7 0 1 0 0 14A7 7 0 0 0 8 1zm0 1.5c.8 0 1.7 1.5 2 4H6c.3-2.5 1.2-4 2-4zM4.6 6.5H2.7a5.5 5.5 0 0 1 3-3.5c-.6 1-1 2.2-1.1 3.5zm0 3c.1 1.3.5 2.5 1.1 3.5a5.5 5.5 0 0 1-3-3.5zM6 9.5h4c-.3 2.5-1.2 4-2 4s-1.7-1.5-2-4zm5.4 0h1.9a5.5 5.5 0 0 1-3 3.5c.6-1 1-2.2 1.1-3.5zm0-3c-.1-1.3-.5-2.5-1.1-3.5a5.5 5.5 0 0 1 3 3.5zM6 8h4M6 8"/></svg>
        www.varkoworks.com
      </li>
      <li>
        <svg viewBox="0 0 16 16"><path d="M1 3.5h14v9H1zM2 4.5l6 4.5 6-4.5v-.5H2z"/></svg>
        martin@plumlinegroup.com
      </li>
      <li>
        <svg viewBox="0 0 16 16"><path d="M8 1a5 5 0 0 0-5 5c0 3.8 5 9 5 9s5-5.2 5-9a5 5 0 0 0-5-5zm0 7a2 2 0 1 1 0-4 2 2 0 0 1 0 4z"/></svg>
        <span>18761 52nd Avenue S<br>Kent, WA 98047</span>
      </li>
    </ul>
  </section>
</body>
</html>
```